Stationery Design Project for Nimbora, Chicago

Nimbora, a street parking application which helps car drivers find a street parking spot by offering an ideal path along which to look for parking. This path is calculated by our algorithm based on data (e.g. historical data, baseball games schedule, etc.). Along this path the driver will find a spot and will also save 70% of the search time. Customer we target is reg. between 21 and 45 yo.

We envision something young, fresh, bright and original. Slightly abstract maybe. It should represent the idea and elements of finding street parking in the city, e.g. car(s), parking spot, people, city, etc. (just ideas!).

Logo is attached.

Requirement:
- Business Cards (2 Sided Full Color CMYK)
- Letterhead (1 Sided Full Color CMYK)
- Envelope (1 Sided Full Color CMYK)
- Sticker (1 Sided Full Color CMYK), round with a 2inch diameter.

Reason: We're starting to get more and more designs and need more time to look into all of them. Very exciting!! Thanks to everybody!

Hi all, we're in the process of selecting our favs. Though choices!!! Really good submissions. Will keep you posted and sorry for the delay.

Target Market(s)

Car drivers and owners between 21 and 45

Industry/Entity Type

Parking

Requirements
Must have
• Sticker should be round and include company URL nimbora.com and the new logo which we will attach soon.
Should not have
• Should not be too serious or boring.

```html
<!DOCTYPE html>
<html lang="en">
<head>
<meta charset="utf-8">
<title>Nimbora business card</title>
<link rel="stylesheet" href="https://fonts.googleapis.com/css2?family=Source+Sans+3:wght@400;600;700&display=swap">
<style>
  :root {
    --backdrop: #e6e7e9;
    --card: #ffffff;
    --ink: #1a1a1a;
    --text-grey: #555559;
    --rule-dark: #2f3138;
    --band-blue: #1d3a9b;
    --mark-blue: #1f5fc8;
    --accent-blue: #2aa7e8;
  }
  * { box-sizing: border-box; margin: 0; padding: 0; }
  html, body { width: 954px; height: 1200px; overflow: hidden; }
  body {
    position: relative;
    background: var(--backdrop);
    font-family: "Source Sans 3", "Myriad Pro", Arial, sans-serif;
  }
  .card {
    position: absolute;
    left: 88px;
    width: 796px;
    height: 455px;
    background: var(--card);
    border-radius: 30px;
    overflow: hidden;
  }
  .card--front { top: 100px; }
  .card--back { top: 643px; }

  .brand { position: absolute; left: 0; top: 0; width: 100%; height: 300px; }
  .brand__dot {
    position: absolute;
    left: 127px; top: 55px;
    width: 150px; height: 150px;
    border-radius: 50%;
    background: var(--mark-blue);
  }
  .brand__name {
    position: absolute;
    left: 300px; top: 58px;
    font-size: 110px;
    font-weight: 600;
    line-height: 1;
    letter-spacing: 1px;
    color: var(--ink);
  }

  .identity {
    position: absolute;
    right: 429px; top: 270px;
    text-align: right;
    color: var(--text-grey);
    font-weight: 700;
  }
  .identity__name { font-size: 27px; line-height: 32px; }
  .identity__role { font-size: 19px; line-height: 26px; }

  .divider {
    position: absolute;
    left: 395px; top: 262px;
    width: 3px; height: 82px;
    background: linear-gradient(to bottom, rgba(42,167,232,0), var(--accent-blue) 50%, rgba(42,167,232,0));
  }

  .contacts {
    position: absolute;
    left: 421px; top: 253px;
    list-style: none;
    color: var(--text-grey);
    font-size: 20px;
    line-height: 26.5px;
  }
  .contacts b { font-weight: 700; }

  .footer-rule {
    position: absolute;
    left: 0; top: 390px;
    width: 100%; height: 4px;
    background: var(--rule-dark);
  }
  .footer-band {
    position: absolute;
    left: 0; top: 397px;
    width: 100%; height: 58px;
    background: var(--band-blue);
    color: #ffffff;
    font-size: 20px;
    line-height: 56px;
    text-align: center;
  }
</style>
</head>
<body>

  <section class="card card--front">
    <div class="brand">
      <span class="brand__dot"></span>
      <span class="brand__name">nimbora</span>
    </div>

    <div class="identity">
      <p class="identity__name">Your Name</p>
      <p class="identity__role">Designation</p>
    </div>

    <span class="divider"></span>

    <ul class="contacts">
      <li><b>p</b> : 123-456-7890</li>
      <li><b>c</b> : 123-456-7890</li>
      <li><b>e</b> : name@website.com</li>
      <li><b>w</b> : www.website.com</li>
    </ul>

    <span class="footer-rule"></span>
    <p class="footer-band">City Name, Street Name, State Name, Country Code</p>
  </section>

  <section class="card card--back">
    <div class="brand" style="top: 0;">
      <span class="brand__dot" style="top: 140px;"></span>
      <span class="brand__name" style="top: 143px;">nimbora</span>
    </div>

    <span class="footer-rule"></span>
    <p class="footer-band">City Name, Street Name, State Name, Country Code</p>
  </section>

</body>
</html>
```